Web Design Project

We are looking to for a redesign for www.volketa.com. Volketa Systems is a Managed Service Provider of IT solutions based is Calgary, Alberta, Canada. We are currently expanding into the Edmonton market and would like to lauch our new site with our expansion.
The design should be sleak in style and communicate a professional vision to our clients and prospects.

Thanks,
Dale

Target Market(s)

Small to medium size businesses looking to outsource or complement their IT solutions.

Industry/Entity Type

It Professional

```html
<!DOCTYPE html>
<html lang="en">
<head>
<meta charset="utf-8">
<title>Volketa Systems – Managed IT Service Professionals</title>
<link href="https://fonts.googleapis.com/css2?family=Source+Sans+3:wght@400;600;700&family=PT+Sans+Narrow:wght@400;700&display=swap" rel="stylesheet">
<style>
:root{
  --black:#0b0b0b;
  --red:#c8121b;
  --red-dark:#9d0c12;
  --hero-bg:#e6e6e6;
  --dark:#262626;
  --panel:#1c1c1c;
  --light-strip:#d2d2d2;
  --text-gray:#8a8a8a;
  --text-light:#b8b8b8;
  --white:#ffffff;
  --ink:#1a1a1a;
  --social:#3a3a3a;
}
*{margin:0;padding:0;box-sizing:border-box}
html,body{width:910px;height:1200px;overflow:hidden}
body{position:relative;font-family:"Source Sans 3",sans-serif;background:var(--hero-bg);color:var(--ink)}
.abs{position:absolute}
.topbar{left:0;top:0;width:910px;height:40px;background:var(--black)}
.topbar .util{left:600px;top:18px;font-size:9px;color:var(--white)}
.topbar .util span{margin:0 5px;color:#777}
.hero{left:0;top:40px;width:910px;height:454px;background:radial-gradient(ellipse at 60% 40%,#f6f6f6 0%,#e2e2e2 60%,#d4d4d4 100%)}
.logo{left:146px;top:62px;display:flex;align-items:center;gap:10px}
.logo .mark{width:26px;height:26px;background:var(--red)}
.logo .name{font-size:28px;font-weight:600;color:var(--ink);line-height:1}
.search{left:516px;top:76px;width:198px;height:23px;background:var(--white);border-radius:6px;box-shadow:1px 2px 3px rgba(0,0,0,.25);font-size:9px;font-style:italic;color:#888;padding:6px 12px}
.hero-title{left:210px;top:196px;color:var(--red);font-weight:700;line-height:1}
.hero-title .line1{font-size:29px;display:block}
.hero-title .line2{font-size:45px;display:block;margin-top:2px}
.hero-copy{left:209px;top:276px;width:276px;font-size:13px;line-height:20.4px;color:var(--text-gray);text-align:justify}
.server-photo{left:504px;top:176px;width:156px;height:224px;border-radius:4px;background:linear-gradient(100deg,#3a3a3a,#111 45%,#1c1c1c)}
.arrow{top:254px;width:32px;height:36px}
.arrow.prev{left:136px}.arrow.next{left:740px}
.nav-line{left:0;top:467px;width:910px;height:6px;background:var(--red-dark)}
.nav{left:133px;top:431px;width:641px;height:42px;background:linear-gradient(var(--red),var(--red-dark));border-radius:6px 6px 0 0}
.nav a{position:absolute;top:11px;color:var(--white);text-decoration:none;font-size:15px;transform:translateX(-50%);white-space:nowrap}
.nav a svg{vertical-align:middle;margin-left:3px}
.main{left:0;top:494px;width:910px;height:492px;background:var(--dark)}
.about-photo{left:146px;top:530px;width:177px;height:116px;border:4px solid var(--white);background:linear-gradient(135deg,#dfe5e8,#9aa3a8 60%,#5d6266)}
.about-title{left:344px;top:530px;font-size:21px;font-weight:600;color:var(--white)}
.about-copy{left:344px;top:561px;width:425px;font-size:7px;line-height:13.5px;color:var(--text-light);text-align:justify}
.read-more{left:675px;top:624px;width:93px;height:18px;background:#d4d4d4;color:var(--ink);font-size:8.5px;text-align:center;line-height:18px}
.panel{top:686px;width:190px;height:262px;background:var(--panel)}
.panel .head{position:absolute;left:0;top:32px;width:150px;height:25px;background:var(--light-strip);font-size:16px;color:var(--ink);padding:3px 18px;letter-spacing:.5px;white-space:nowrap}
.panel .icon-box{position:absolute;right:0;top:16px;width:50px;height:58px;background:var(--light-strip);border-radius:5px;display:flex;align-items:center;justify-content:center}
.spotlight{left:130px}.partners{left:361px}.support{left:596px}
.spotlight .copy{position:absolute;left:10px;top:106px;width:76px;font-size:12px;line-height:15.3px;color:var(--white)}
.spotlight .rack{position:absolute;left:94px;top:90px;width:80px;height:96px;background:linear-gradient(90deg,#0f1a24,#2c5a7a 50%,#0c1218)}
.partner-badge{position:absolute;left:25px;width:138px}
.badge-a{top:88px;height:32px;background:var(--white)}
.badge-b{top:132px;height:46px;background:var(--red)}
.badge-c{top:188px;height:48px;background:#1b87cf}
.scroll-track{position:absolute;left:174px;top:82px;width:1px;height:150px;border-left:1px dotted #888}
.scroll-thumb{position:absolute;left:171px;width:7px;height:16px;border-radius:3px}
.support .photo{position:absolute;left:36px;top:83px;width:123px;height:101px;background:linear-gradient(160deg,#ffffff,#e4e4e4 55%,#3a3a3a)}
.support .cta{position:absolute;left:30px;top:212px;font-size:12px;line-height:15.5px;color:var(--white);text-align:center}
.support .live{position:absolute;left:104px;top:192px;font-size:34px;color:var(--red);line-height:1;letter-spacing:1px}
.support .live-sub{position:absolute;left:104px;top:224px;font-size:17px;color:var(--white);letter-spacing:.5px}
.footer{left:0;top:986px;width:910px;height:168px;background:linear-gradient(#cfcfcf,#e6e6e6 40%,#d0d0d0)}
.call{left:158px;top:1024px;font-family:"PT Sans Narrow",sans-serif;font-weight:700;font-size:29px;line-height:30px;color:var(--ink)}
.call .phone{display:block;color:var(--red);font-size:25px;margin-top:4px}
.links{top:1006px;list-style:none;font-size:8.5px;line-height:20px;color:var(--ink)}
.links.c1{left:325px}.links.c2{left:433px}.links.c3{left:527px}
.social{top:1108px;width:32px;height:32px;border-radius:50%;background:var(--social)}
.social.first{background:var(--red)}
.bottombar{left:0;top:1154px;width:910px;height:46px;background:var(--black);color:var(--white);font-size:8.5px}
.bottombar span{position:absolute;top:14px}
</style>
</head>
<body>
<div class="abs topbar"><div class="abs util">Help<span>|</span>Support</div></div>

<div class="abs hero"></div>
<div class="abs logo"><div class="mark"></div><div class="name">Volketa</div></div>
<div class="abs search">Search</div>

<h1 class="abs hero-title"><span class="line1">Managed IT Service</span><span class="line2">Professionals</span></h1>
<p class="abs hero-copy">Volketa Systems employs an innovative managed service solution to provide our clients with technical expertise and superb customer service. Our goal is to ensure that our clients business requirements align with their technical needs in</p>
<div class="abs server-photo" role="img" aria-label="Black tower server unit"></div>

<svg class="abs arrow prev" viewBox="0 0 32 36"><path d="M24 2 L6 18 L24 34 L30 34 L14 18 L30 2Z" fill="#333"/></svg>
<svg class="abs arrow next" viewBox="0 0 32 36"><path d="M8 2 L26 18 L8 34 L2 34 L18 18 L2 2Z" fill="#333"/></svg>

<div class="abs nav-line"></div>
<nav class="abs nav">
  <a style="left:81px">About us</a>
  <a style="left:219px">Solutions<svg width="9" height="6" viewBox="0 0 9 6"><path d="M1 1 L4.5 4.5 L8 1" stroke="#fff" stroke-width="1.8" fill="none"/></svg></a>
  <a style="left:349px">Services<svg width="9" height="6" viewBox="0 0 9 6"><path d="M1 1 L4.5 4.5 L8 1" stroke="#fff" stroke-width="1.8" fill="none"/></svg></a>
  <a style="left:466px">Careers</a>
  <a style="left:589px">Contact</a>
</nav>

<main class="abs main"></main>
<div class="abs about-photo" role="img" aria-label="Businessman working at a laptop in a bright office"></div>
<h2 class="abs about-title">About Us</h2>
<p class="abs about-copy">Is simply dummy text of the printing and typesetting industry. Lorem Ipsum has been the industry's standard dummy text ever ince the 1500s, when an unknown printer took a galley of type and scrambled it to make a type specimen book. It has survived not only five centuries, but also the leap into electronic typesetting, remaining essentially unchanged. It was popularised in the 1960s with he release of Printwell sheets containing Lorem Ipsum passages, and more recently with desktop publishing software like Pagecraft Studio including versions of Lorem Ipsum.</p>
<div class="abs read-more">READ MORE &gt;&gt;&gt;</div>

<section class="abs panel spotlight">
  <div class="head">SPOTLIGHT</div>
  <div class="icon-box"><svg width="22" height="30" viewBox="0 0 22 30"><circle cx="11" cy="10" r="9" fill="#111"/><rect x="7" y="18" width="8" height="8" fill="#111"/><rect x="8" y="27" width="6" height="2" fill="#111"/></svg></div>
  <p class="copy">Keep your data secure and readily available with our online backup service</p>
  <div class="rack" role="img" aria-label="Server racks glowing blue"></div>
</section>

<section class="abs panel partners">
  <div class="head">PARTNERS</div>
  <div class="icon-box"><svg width="38" height="40" viewBox="0 0 38 40"><circle cx="19" cy="6" r="4" fill="#111"/><rect x="14" y="11" width="10" height="26" rx="2" fill="#111"/><circle cx="7" cy="6" r="3" fill="#111"/><rect x="3" y="10" width="8" height="18" rx="2" fill="#111"/><circle cx="31" cy="6" r="3" fill="#111"/><rect x="27" y="10" width="8" height="18" rx="2" fill="#111"/></svg></div>
  <div class="partner-badge badge-a"></div>
  <div class="partner-badge badge-b"></div>
  <div class="partner-badge badge-c"></div>
  <div class="scroll-track"></div>
  <div class="scroll-thumb" style="top:82px;background:#fff"></div>
  <div class="scroll-thumb" style="top:232px;background:#777"></div>
</section>

<section class="abs panel support">
  <div class="head">LIVE SUPPORT</div>
  <div class="icon-box"><svg width="32" height="32" viewBox="0 0 32 32"><rect x="1" y="1" width="30" height="30" rx="5" fill="#111"/><path d="M11 7 C8 9 8 14 12 20 C16 26 20 27 23 25 L21 21 L18 22 C16 21 14 17 14 15 L16 13 Z" fill="#fff"/></svg></div>
  <div class="photo" role="img" aria-label="Support agent at a laptop"></div>
  <p class="cta">Click here to<br>access our</p>
  <div class="live">LIVE</div>
  <div class="live-sub">SUPPORT</div>
</section>

<footer class="abs footer"></footer>
<div class="abs call">Call US<br>TOLL FREE @<span class="phone">(800)555-0147</span></div>
<ul class="abs links c1"><li>About Us</li><li>Company Info</li><li>Clients</li><li>Partners</li><li>Marketing</li><li>Management</li></ul>
<ul class="abs links c2"><li>Forums</li><li>Promotions</li><li>Marketing</li></ul>
<ul class="abs links c3"><li>FAQ</li><li>Solutions</li><li>Services</li></ul>
<div class="abs social first" style="left:610px"></div>
<div class="abs social" style="left:652px"></div>
<div class="abs social" style="left:696px"></div>
<div class="abs social" style="left:742px"></div>

<div class="abs bottombar">
  <span style="left:134px">2012 @ Volketa ,All Rights Reserved</span>
  <span style="left:494px">About us</span>
  <span style="left:566px">Terms &amp; Conditions</span>
  <span style="left:679px">Careers</span>
  <span style="left:746px">Contact</span>
</div>
</body>
</html>
```